Vertical Banner

I need an eye-catching banner created for street fairs, indoor and outdoor events to draw attention to our language school. It will be to print on this banner (specs included):
https://www.banvoxprint.com/tag/617/Retractable-Banners/product/5174-46/Economy-Retractor-Banner-Display-27-09

I want the banner to be:
- SIMPLE
- Eye catching (not busy with too many pictures or information)
- It should say at top prominently: "Come learn a language!" and have our name.
- Below these languages should be large and eye-catching: Spanish, Chinese, French, Russian, German, Italian, Farsi, Turkish, Portuguese, ASL, Cantonese, Japanese, Korean, Vietnamese, Arabic, Dutch, more... (if some need to be cut our because of overcrowding let me know OR we can make some big and others small)
- Below this it should have GROUP & PRIVATE LESSONS
- It should be colorful and make people think of things international - perhaps national flags in background? Or images of world famous monuments? Could be image of adutls in a classroom. Sth that gets people excited about travel and language learning
- It should have our contact info VERY large at bottom:
Tovira Languages -
San Francisco, Silicon Valley & New York City
www.toviralanguagesf.com
415-629-5140
info@toviralanguagesf.com
(this can be smaller)
Four Wexmoor Plaza
Lobby 3
San Francisco, CA 94187

Hey Designers, please feel free to do a rough take on it. I don't need you to spend too much time, just give me a general idea of how you would make it look, then i know we can go from there later and refine it. Feel free to make it more of a quick sketch to show how you would do it.

Target Market(s)

adults from about 25-55 years old, educated, employed and typically world travellers

Industry/Entity Type

School

Colors
86cfc6
00a990
cadf82
acd036
9bcb3c
fbed22
f78f20
ffc214
f37122

Requirements
Must have
• Must be simple! Too many banners put way too much information and pictures. I want someone to walk by and immediately know we teach foreign languages. Must have bright colors and large font for languages offered
Should not have
• Should not be too full of images and design that distract the viewer from seeing the main thing I want them to see: that we teacher languages

```html
<!DOCTYPE html>
<html lang="en">
<head>
<meta charset="utf-8">
<title>Tovira Languages – Vertical Banner</title>
<link rel="stylesheet" href="https://fonts.googleapis.com/css2?family=Open+Sans:wght@400;700;800&family=PT+Sans+Narrow:wght@400;700&display=swap">
<style>
  :root {
    --page-bg: #e6e6e6;
    --teal-band: #42828f;
    --green: #52b848;
    --black: #0a0a0a;
    --white: #ffffff;
    --sky-light: #e9f6f5;
    --sky: #9dd8d8;
    --skyline: #4d8797;
    --ring: #5aa39a;
    --ink: #111111;
    --deep: #003a47;
    --accent-red: #e52b2b;
    --label: #1f3a44;
  }
  * { margin: 0; padding: 0; box-sizing: border-box; }
  html, body { width: 1200px; height: 1200px; overflow: hidden; }
  body { background: var(--page-bg); position: relative; font-family: "Open Sans", sans-serif; }

  .banner {
    position: absolute; left: 381px; top: 20px;
    width: 493px; height: 1303px;
    transform: scale(0.89); transform-origin: top left;
    background: linear-gradient(to bottom, var(--white) 0, var(--white) 380px, var(--sky-light) 440px, var(--sky) 620px, var(--sky) 100%);
    overflow: hidden;
  }
  .band { position: absolute; left: 0; width: 100%; color: var(--white); text-align: center; font-weight: 700; }
  .band--come { top: 0; height: 83px; background: var(--teal-band); font-size: 50px; letter-spacing: 28px; padding-left: 28px; line-height: 100px; font-weight: 400; }
  .band--learn { top: 83px; height: 83px; background: var(--green); font-size: 68px; line-height: 83px; }
  .band--language { top: 166px; height: 82px; background: var(--black); font-size: 64px; line-height: 82px; }

  .brand { position: absolute; top: 262px; width: 100%; text-align: center; color: var(--ink); font-weight: 800; }
  .brand__line1 { display: block; font-size: 92px; line-height: 110px; letter-spacing: -1px; }
  .brand__line2 { display: block; font-size: 56px; line-height: 64px; }

  .skyline { position: absolute; left: 0; top: 440px; width: 493px; height: 520px; }

  .language-list {
    position: absolute; left: 58px; top: 540px; width: 370px; height: 370px;
    display: flex; flex-direction: column; align-items: center; justify-content: center;
    color: var(--ink); line-height: 1;
  }
  .row { display: flex; align-items: baseline; gap: 8px; margin: 1px 0; }
  .w-bold { font-family: "Open Sans", sans-serif; font-weight: 800; }
  .w-narrow { font-family: "PT Sans Narrow", sans-serif; font-weight: 400; }
  .w-narrow-bold { font-family: "PT Sans Narrow", sans-serif; font-weight: 700; }
  .more { color: var(--accent-red); font-style: italic; font-weight: 700; font-size: 22px; }

  .lessons-label {
    position: absolute; top: 980px; width: 100%; text-align: center;
    font-family: "PT Sans Narrow", sans-serif; font-weight: 700; font-size: 30px; line-height: 42px; color: var(--label);
  }
  .lesson-icon { position: absolute; }

  .contact {
    position: absolute; left: 0; bottom: 0; width: 100%; height: 240px;
    color: var(--white); text-align: center; font-family: "PT Sans Narrow", sans-serif; font-weight: 700;
  }
  .contact__shape { position: absolute; inset: 0; }
  .contact__text { position: relative; padding-top: 48px; }
  .contact__name { font-size: 42px; line-height: 50px; }
  .contact__cities { font-size: 23px; line-height: 34px; }
  .contact__reach { font-size: 27px; line-height: 46px; }
  .contact__reach .sep { margin: 0 10px; }
  .contact__web { font-size: 40px; line-height: 40px; }
</style>
</head>
<body>
  <main class="banner">
    <div class="band band--come">COME</div>
    <div class="band band--learn">LEARN A</div>
    <div class="band band--language">LANGUAGE</div>

    <div class="brand">
      <span class="brand__line1">Tovira</span>
      <span class="brand__line2">LANGUAGES</span>
    </div>

    <svg class="skyline" viewBox="0 0 493 520" role="img" aria-label="Illustration of world landmarks, clouds, hot-air balloons and planes circling the globe">
      <ellipse cx="243" cy="285" rx="240" ry="255" fill="var(--skyline)" opacity="0.55"/>
      <ellipse cx="243" cy="285" rx="205" ry="210" fill="#cfeceb" opacity="0.8"/>
      <circle cx="243" cy="285" r="186" fill="var(--white)" stroke="var(--ring)" stroke-width="4"/>
    </svg>

    <div class="language-list">
      <div class="row"><span class="w-bold" style="font-size:38px">FRENCH</span></div>
      <div class="row"><span class="w-bold" style="font-size:32px">CHINESE</span><span class="w-narrow" style="font-size:26px">TURKISH</span></div>
      <div class="row"><span class="w-bold" style="font-size:30px">SPANISH</span><span class="w-narrow" style="font-size:40px">GERMAN</span></div>
      <div class="row"><span class="w-narrow" style="font-size:44px">ITALIAN</span><span class="w-bold" style="font-size:30px">FARSI</span></div>
      <div class="row"><span class="w-bold" style="font-size:30px">ASL</span><span class="w-bold" style="font-size:38px">RUSSIAN</span></div>
      <div class="row"><span class="w-narrow" style="font-size:24px;letter-spacing:9px">PORTUGUESE</span></div>
      <div class="row"><span class="w-narrow-bold" style="font-size:42px">JAPANESE</span><span class="w-bold" style="font-size:22px">CANTONESE</span></div>
      <div class="row"><span class="w-bold" style="font-size:30px">KOREAN</span><span class="w-narrow" style="font-size:32px">ARABIC</span></div>
      <div class="row"><span class="w-narrow" style="font-size:24px">VIETNAMESE</span><span class="w-narrow" style="font-size:32px">DUTCH</span></div>
      <div class="row"><span class="more">MORE.....</span></div>
    </div>

    <svg class="lesson-icon" style="left:42px;top:935px" width="106" height="106" viewBox="0 0 106 106" role="img" aria-label="Icon of a teacher presenting to a group of students">
      <circle cx="53" cy="53" r="53" fill="#e8f4f3"/>
    </svg>
    <svg class="lesson-icon" style="left:352px;top:938px" width="106" height="106" viewBox="0 0 106 106" role="img" aria-label="Icon of a tutor and a student at a desk">
      <circle cx="53" cy="53" r="53" fill="var(--white)"/>
    </svg>

    <div class="lessons-label">GROUP &amp;<br>PRIVATE LESSONS</div>

    <section class="contact">
      <svg class="contact__shape" viewBox="0 0 493 240" preserveAspectRatio="none" aria-hidden="true">
        <path d="M0 12 Q246 -18 493 12 L493 240 L0 240 Z" fill="var(--deep)"/>
      </svg>
      <div class="contact__text">
        <div class="contact__name">Tovira Languages</div>
        <div class="contact__cities">San Francisco, Silicon Valley &amp; New York City</div>
        <div class="contact__reach">415-629-5140<span class="sep">|</span>info@toviralanguagesf.com</div>
        <div class="contact__web">www.toviralanguagesf.com</div>
      </div>
    </section>
  </main>
</body>
</html>
```